Quintara Legal Letterhead

Need a new letterhead for my law firm.
IDENTIFYING INFORMATION BELOW:
Anselmo R Quintara III
Attorney at Law
Address: 2847 Larkspur Blvd, Ste 300, Dallas, TX 75204
Phone: 877-482-6017
Fax: 469-738-1452
Email: aq@quintara.example
Website: www.quintara.example

Colors
0054AA
0677BA
7BADD7
CADEEF
E8F1F8

Requirements
Must have
• Logo needs to be on the letterhead, along with identifying information which is included in the project description.

```html
<!DOCTYPE html>
<html lang="en">
<head>
<meta charset="utf-8">
<title>Quintara Legal Letterhead</title>
<link rel="stylesheet" href="https://fonts.googleapis.com/css2?family=Montserrat:wght@300;400;800&display=swap">
<style>
  :root {
    --stage: #2a2a2a;
    --paper: #ffffff;
    --ink: #1a1a1a;
    --text: #2b2b2b;
    --footer: #222222;
    --blue-deep: #0054AA;
    --blue: #0677BA;
    --blue-light: #7BADD7;
    --footer-text: #f2f2f2;
  }
  * { margin: 0; padding: 0; box-sizing: border-box; }
  html, body { width: 1200px; height: 1059px; overflow: hidden; background: var(--stage); }
  body { position: relative; font-family: "Montserrat", sans-serif; }

  .letterhead {
    position: absolute; left: 306px; top: 113px;
    width: 588px; height: 832px;
    background: var(--paper);
  }
  .brand {
    position: absolute; left: 0; right: 0; top: 48px;
    text-align: center; color: var(--ink);
  }
  .brand-name {
    font-weight: 800; font-size: 28px; letter-spacing: 1px; line-height: 34px;
    text-transform: uppercase;
  }
  .brand-tagline {
    font-weight: 300; font-size: 15px; letter-spacing: 2.6px; line-height: 18px;
  }

  .letter-body {
    position: absolute; left: 35px; top: 204px; width: 519px;
    font-size: 10.8px; line-height: 16.9px; letter-spacing: 0.15px;
    color: var(--text); font-weight: 400;
  }
  .recipient { margin-bottom: 1px; }
  .letter-body p { text-align: justify; }
  .para-1 { margin-bottom: 18px; }
  .para-2 { margin-bottom: 15px; }
  .para-3 { margin-bottom: 10px; }

  .signature {
    position: absolute; left: 35px; top: 579px; width: 107px; height: 44px;
    background: linear-gradient(90deg, #e4e4e4, #f3f3f3);
  }

  .footer {
    position: absolute; left: 0; bottom: 0; width: 588px; height: 47px;
    background: var(--footer); color: var(--footer-text);
    font-size: 10.8px; line-height: 14.7px;
  }
  .footer-mark {
    position: absolute; left: 0; top: 0; width: 47px; height: 47px;
    background: linear-gradient(135deg, var(--blue-light), var(--blue) 55%, var(--blue-deep));
  }
  .contact-col { position: absolute; top: 9px; }
  .contact-col.phones { left: 88px; }
  .contact-col.web { left: 249px; }
  .contact-col.address { left: 416px; }
  .contact-line { display: flex; align-items: center; gap: 5px; white-space: nowrap; }
  .contact-line svg { width: 9px; height: 9px; fill: var(--blue); flex: none; }
  .divider {
    position: absolute; top: 11px; width: 1px; height: 25px; background: var(--blue);
  }
  .divider.first { left: 219px; }
  .divider.second { left: 390px; }
</style>
</head>
<body>
  <main class="letterhead">
    <header class="brand">
      <div class="brand-name">Quintara Legal</div>
      <div class="brand-tagline">ATTORNEY AT LAW</div>
    </header>

    <section class="letter-body">
      <div class="recipient">Mr/s<br>First Name and Last Name<br>Company Name<br>Address</div>
      <p class="para-1">Lorem Ipsum is simply dummy text of the printing and typesetting industry. Lorem Ipsum has been the industry's standard dummy text ever since the 1500s, when an unknown printer took a galley of type and scrambled it to make a type specimen book. It has survived not only five centuries, but also the leap into electronic typesetting, remaining essentially unchanged. It was popularised in the 1960s.</p>
      <p class="para-2">The standard chunk of Lorem Ipsum used since the 1500s is reproduced below for those interested. Sections 1.10.32 and 1.10.33 from "de Finibus Bonorum et Malorum" by Cicero are also reproduced in their exact original form, accompanied by English versions from the 1914 translation by H. Rackham. Lorem ipsum dolor sit amet, consectetur adipiscing elit, sed do eiusmod tempor incididunt ut labore et dolore magna aliqua.</p>
      <p class="para-3">It is a long established fact that a reader will be distracted by the readable content of a page when looking at its layout. The point of using Lorem Ipsum is that it has a more-or-less normal distribution of letters, as opposed to using 'Content here, content here', making it look like readable English. Many desktop publishing packages and web page editors now .</p>
      <div class="closing">Your Sincerely,</div>
    </section>

    <div class="signature" role="img" aria-label="Handwritten signature"></div>

    <footer class="footer">
      <div class="footer-mark"></div>
      <div class="contact-col phones">
        <div class="contact-line">
          <svg viewBox="0 0 10 10"><path d="M2 0.5 L3.6 2.6 L2.8 3.6 C3.4 5 4.8 6.4 6.4 7.1 L7.4 6.3 L9.5 7.9 L8.4 9.5 C4.5 9.2 0.8 5.5 0.5 1.6 Z"/></svg>
          <span>877-482-6017</span>
        </div>
        <div class="contact-line">
          <svg viewBox="0 0 10 10"><rect x="2.5" y="0.5" width="5" height="2.5"/><rect x="0.5" y="3.5" width="9" height="4" rx="0.8"/><rect x="2.5" y="6.5" width="5" height="3"/></svg>
          <span>469-738-1452</span>
        </div>
      </div>
      <div class="divider first"></div>
      <div class="contact-col web">
        <div class="contact-line">
          <svg viewBox="0 0 10 10"><rect x="0.5" y="2" width="9" height="6.5"/><path d="M0.5 2 L5 5.8 L9.5 2" fill="none" stroke="#222" stroke-width="0.9"/></svg>
          <span>aq@quintara.example</span>
        </div>
        <div class="contact-line">
          <svg viewBox="0 0 10 10"><circle cx="5" cy="5" r="4.5"/><path d="M0.8 5 H9.2 M5 0.6 C3 3 3 7 5 9.4 M5 0.6 C7 3 7 7 5 9.4" fill="none" stroke="#222" stroke-width="0.7"/></svg>
          <span>www.quintara.example</span>
        </div>
      </div>
      <div class="divider second"></div>
      <div class="contact-col address">
        <div>2847 Larkspur Blvd,</div>
        <div>Ste 300, Dallas, TX 75204</div>
      </div>
    </footer>
  </main>
</body>
</html>
```